lantern pathway for children needs a website designer

We need a website designer for our new extension to our company known as 'lantern pathway' providing shadow support services to children based in Singapore. We are a sister branch of a private clinic 'Bright horizons' providing speech language, occupational, and educational therapy to children.

We would like to use our own photos. So the selected design should have a frame with pictures to give us an idea but we will replace them with our own. We will be needing help with inputting information and changing information throughout.

We would like to see designs that are simple, and professional. We have a logo (see attached). The result should convey professionalism in shadow support, fostering independent thinking and moving students towards self-learning.

Target Market(s)

Teachers, psychologists, parents

Industry/Entity Type

Clinic

Requirements
Should not have
• too distracting colours

```html
<!DOCTYPE html>
<html lang="en">
<head>
<meta charset="utf-8">
<title>Lantern Pathway – Shadow Support</title>
<link href="https://fonts.googleapis.com/css2?family=Arimo:wght@400;700&display=swap" rel="stylesheet">
<style>
:root{
  --maroon:#8a0f14;
  --red-grad-top:#b52025;
  --red-grad-bot:#7c0c10;
  --ink:#555;
  --muted:#a3a3a3;
  --rule:#c9c9c9;
  --footer:#6b6b6b;
  --white:#fff;
}
*{margin:0;padding:0;box-sizing:border-box}
html,body{width:706px;height:1200px;overflow:hidden;background:var(--white);font-family:"Arimo",Arial,sans-serif}
h2,h3{font-weight:400}
.page{position:relative;width:706px;height:1200px}
.abs{position:absolute}

.brand{left:82px;top:36px;display:flex;align-items:center;gap:8px}
.brand-dot{width:16px;height:16px;border-radius:50%;background:var(--maroon)}
.brand-name{font-size:24px;font-weight:700;color:var(--maroon);letter-spacing:-.3px}

.contact{left:453px;top:20px;font-size:8.5px;line-height:18px;color:var(--ink)}
.contact b{font-weight:400;color:var(--maroon)}

.nav{left:0;top:90px;width:706px;height:25px;background:linear-gradient(var(--red-grad-top),var(--red-grad-bot));border-top:1px solid #d44}
.nav a{position:absolute;top:7px;font-size:9.5px;color:var(--white);text-decoration:none}
.search{left:510px;top:4px;width:108px;height:16px;border-radius:4px;background:#f4f4f4;font-size:6.5px;color:#999;padding:4px 5px}
.search svg{position:absolute;right:6px;top:4px}

.hero{left:0;top:117px;width:706px;height:305px;background:linear-gradient(100deg,#e8ede8 0%,#d8cfc3 35%,#e3cbb7 60%,#b9d7b3 100%)}
.hero-arrow{top:128px}
.caption{left:0;top:267px;width:706px;height:38px;background:rgba(70,70,70,.55)}
.caption p{position:absolute;left:91px;top:8px;width:340px;font-size:8.5px;line-height:15px;color:var(--white)}
.register{left:481px;top:9px;width:134px;height:21px;border-radius:3px;background:#f6f6f6;font-size:9.5px;color:var(--maroon);text-align:center;line-height:21px}
.hero-shadow{left:60px;top:422px;width:586px;height:12px;background:radial-gradient(ellipse at top,rgba(0,0,0,.12),transparent 70%)}

.section-title{width:706px;left:0;text-align:center;font-size:15px;color:var(--maroon)}
.about-text{left:99px;top:471px;width:510px;text-align:center;font-size:6.6px;line-height:14.4px;color:var(--muted)}

.service-photo{border-radius:5px}
.service-title{width:170px;text-align:center;font-size:11px;color:var(--ink)}
.service-text{width:160px;text-align:center;font-size:6.6px;line-height:14.4px;color:var(--muted)}
.btn{height:24px;border-radius:4px;background:linear-gradient(var(--red-grad-top),var(--red-grad-bot));color:var(--white);font-size:7.5px;text-align:center;line-height:24px;box-shadow:0 1px 2px rgba(0,0,0,.3)}

.faq-title{left:83px;font-size:10.5px;color:var(--maroon)}
.faq-text{left:83px;width:242px;font-size:6.6px;line-height:14.4px;color:var(--muted)}
.faq-text span{color:var(--maroon);font-size:7.3px}
.rule{left:83px;width:255px;height:1px;background:var(--rule)}

.testi-title{left:382px;top:826px;font-size:10.5px;color:var(--maroon)}
.avatar{width:80px;height:80px;border-radius:50%;border:3px solid #d8d8d8;background:linear-gradient(#e9e9e9,#c9c9c9)}
.quote{left:468px;width:156px;font-size:6.6px;line-height:14.4px;color:var(--muted)}
.quote-name{left:470px;width:152px;text-align:right;font-size:6.8px;color:var(--maroon)}

.footer{left:0;top:1112px;width:706px;height:88px;background:var(--footer)}
.social{top:10px;width:22px;height:22px;border-radius:50%;background:#888;border:2px solid #e5e5e5}
.foot-links{left:0;top:42px;width:706px;text-align:center;font-size:7.3px;color:var(--white)}
.foot-links i{font-style:normal;margin:0 8px}
.copyright{left:0;top:65px;width:706px;text-align:center;font-size:6.3px;color:#ddd}
</style>
</head>
<body>
<div class="page">

  <div class="abs brand"><span class="brand-dot"></span><span class="brand-name">Lantern Pathway</span></div>
  <div class="abs contact">
    <b>Make An Enquiry</b><br>
    <b>Call</b> +65 6100 2040<br>
    <b>E-mail</b> :enquiries@brightfordtherapy.sg
  </div>

  <nav class="abs nav">
    <a style="left:102px">Home</a>
    <a style="left:165px">About us</a>
    <a style="left:239px">Testimonials</a>
    <a style="left:328px">Shadow Support</a>
    <a style="left:433px">Contact us</a>
    <div class="abs search">Search
      <svg width="8" height="8" viewBox="0 0 8 8"><circle cx="3" cy="3" r="2.2" fill="none" stroke="#888" stroke-width="1"/><line x1="4.6" y1="4.6" x2="7.5" y2="7.5" stroke="#888" stroke-width="1.2"/></svg>
    </div>
  </nav>

  <div class="abs hero" role="img" aria-label="Photo of a therapist playing with finger puppets with a young child">
    <svg class="abs hero-arrow" style="left:32px" width="22" height="22" viewBox="0 0 22 22"><circle cx="11" cy="11" r="10" fill="none" stroke="rgba(255,255,255,.6)" stroke-width="1.5"/><path d="M13 6l-5 5 5 5" fill="none" stroke="rgba(255,255,255,.7)" stroke-width="1.8"/></svg>
    <svg class="abs hero-arrow" style="left:646px" width="22" height="22" viewBox="0 0 22 22"><circle cx="11" cy="11" r="10" fill="none" stroke="rgba(255,255,255,.6)" stroke-width="1.5"/><path d="M9 6l5 5-5 5" fill="none" stroke="rgba(255,255,255,.7)" stroke-width="1.8"/></svg>
    <div class="abs caption">
      <p>A shadow support is para-professional who can help a struggling student to integrate and learn in their school environment.</p>
      <div class="abs register">Register now</div>
    </div>
  </div>
  <div class="abs hero-shadow"></div>

  <h2 class="abs section-title" style="top:441px">About Us</h2>
  <p class="abs about-text">Lantern Pathway is part of the Brightford Therapy Group of Companies, who are providing speech language therapy, occupational therapy and educational therapy services to both the Singapore and the international school community.</p>

  <h2 class="abs section-title" style="top:529px">Our Services</h2>

  <div class="abs service-photo" style="left:83px;top:569px;width:164px;height:107px;background:linear-gradient(120deg,#f0ece6,#d8b9a0 55%,#b99bc8)" role="img" aria-label="Photo of a child and therapist working on a language activity"></div>
  <div class="abs service-photo" style="left:271px;top:569px;width:164px;height:107px;background:linear-gradient(120deg,#c9b79a,#b9a6c5 50%,#c8a070)" role="img" aria-label="Photo of children doing occupational therapy exercises"></div>
  <div class="abs" style="left:456px;top:562px;width:168px;height:121px;background:linear-gradient(160deg,#d8d2d8,#a9a6ad 50%,#cfc2b0)" role="img" aria-label="Photo of a boy and teacher doing an educational game at a table"></div>

  <h3 class="abs service-title" style="left:78px;top:687px">Language Therapy</h3>
  <h3 class="abs service-title" style="left:265px;top:687px">Occupational Therapy</h3>
  <h3 class="abs service-title" style="left:452px;top:687px">Educational Therapy</h3>

  <p class="abs service-text" style="left:83px;top:709px">Lantern Pathway was borne out of our Speech language Pathologists' frustration at a frequent lack of carry-over tings.</p>
  <p class="abs service-text" style="left:270px;top:709px">Lantern Pathway was borne out of our Speech language Pathologists' frustration at a frequent lack of carry-over tings.</p>
  <p class="abs service-text" style="left:457px;top:709px">Lantern Pathway was borne out of our Speech language Pathologists' frustration at a frequent lack of carry-over tings.</p>

  <div class="abs btn" style="left:125px;top:762px;width:73px">Read More</div>
  <div class="abs btn" style="left:313px;top:762px;width:73px">Read More</div>
  <div class="abs btn" style="left:500px;top:762px;width:74px">Read More</div>

  <h3 class="abs faq-title" style="top:826px">What is shadow support?</h3>
  <p class="abs faq-text" style="top:846px">A shadow support is para-professional who can help a struggling student to integrate and learn in their school environment. &nbsp; At different points in a student's life, for a para-professional difference.... &nbsp; <span>Read More</span></p>
  <div class="abs rule" style="top:905px"></div>

  <h3 class="abs faq-title" style="top:912px">What are its Advantages?</h3>
  <p class="abs faq-text" style="top:933px">A fully trained shadow support is an asset to the student who otherwise would have trouble fitting in and adapting to the mainstream school environment. Additionally, working closely with the therapist .... &nbsp; <span>Read More</span></p>
  <div class="abs rule" style="top:992px"></div>

  <h3 class="abs faq-title" style="top:1000px">How do I know if my child needs shadowing</h3>
  <p class="abs faq-text" style="top:1020px">A consultation with our Speech Language Pathologist, along with an assessment by an Educational Psychologist would provide us with an indication of whether the child requires shadowing. &nbsp;.... &nbsp; <span>Read More</span></p>
  <div class="abs rule" style="top:1079px"></div>

  <h3 class="abs testi-title">Testimonials</h3>
  <div class="abs avatar" style="left:379px;top:854px" role="img" aria-label="Portrait of a parent giving a testimonial"></div>
  <p class="abs quote" style="top:865px">❛❛ Lantern Pathway was borne out of our Speech language Pathologists' frustration at a frequent lack of carry-over of goals to a classroom settingdifferent settings ❜❜</p>
  <p class="abs quote-name" style="top:926px">Helen Marsh</p>

  <div class="abs avatar" style="left:379px;top:957px" role="img" aria-label="Portrait of a teacher giving a testimonial"></div>
  <p class="abs quote" style="top:969px">❛❛ Lantern Pathway was borne out of our Speech language Pathologists' frustration at a frequent lack of carry-over of goals to a classroom settingdifferent settings ❜❜</p>
  <p class="abs quote-name" style="top:1030px">Helen Marsh</p>

  <div class="abs btn" style="left:391px;top:1055px;width:72px">View More</div>

  <footer class="abs footer">
    <span class="abs social" style="left:301px"></span>
    <span class="abs social" style="left:327px"></span>
    <span class="abs social" style="left:351px"></span>
    <span class="abs social" style="left:377px"></span>
    <p class="abs foot-links">Home<i>|</i>About us<i>|</i>Testimonials<i>|</i>Shadow Support<i>|</i>Contact us</p>
    <p class="abs copyright">Copyright 2014 Lantern Pathway.All Right Reserved.</p>
  </footer>

</div>
</body>
</html>
```